Modern Business Card

Modern professional business card with more than just logo and demographic info. Something memorable.

We are a trendy/modern chiropractic group with an emphasis on neurology, hence the minimalist-type brain logo. We want to convey that modern and technical aspect with professionalism and the elite nature of our practice environment.

```html
<!DOCTYPE html>
<html lang="en">
<head>
<meta charset="utf-8">
<title>Northvale Spine Care – Business Card</title>
<link href="https://fonts.googleapis.com/css2?family=Cinzel:wght@500&family=Exo+2:wght@600&family=Open+Sans:wght@400&display=swap" rel="stylesheet">
<style>
  :root {
    --backdrop: #3a3a3c;
    --card: #1e1e20;
    --card-edge: #151516;
    --ink-light: #f2f2f2;
    --ink-muted: #d6d6d8;
    --front-mark: #8c8c90;
    --accent-blue: #4a6fb3;
    --band-start: #4c4048;
    --band-end: #4469ad;
  }
  * { margin: 0; padding: 0; box-sizing: border-box; }
  html, body { width: 799px; height: 1200px; overflow: hidden; }
  body {
    background: var(--backdrop);
    font-family: "Open Sans", sans-serif;
    position: relative;
  }
  .card {
    position: absolute;
    left: 80px;
    width: 640px;
    height: 366px;
    background: var(--card);
    border: 1px solid var(--card-edge);
    border-radius: 3px;
    box-shadow: 0 18px 40px rgba(0,0,0,0.45);
    overflow: hidden;
  }
  .card-front { top: 150px; }
  .card-back { top: 690px; }

  .front-name {
    position: absolute;
    inset: 0;
    display: flex;
    align-items: center;
    justify-content: center;
    gap: 18px;
    font-family: "Cinzel", serif;
    font-weight: 500;
    font-size: 34px;
    letter-spacing: 4px;
    color: var(--front-mark);
  }
  .front-name .dot {
    width: 22px; height: 22px;
    border-radius: 50%;
    background: var(--front-mark);
  }

  .wordmark {
    position: absolute;
    left: 40px;
    top: 92px;
    display: flex;
    align-items: center;
    gap: 14px;
  }
  .wordmark .dot {
    width: 26px; height: 26px;
    border-radius: 50%;
    background: var(--accent-blue);
  }
  .wordmark-text {
    font-family: "Cinzel", serif;
    font-weight: 500;
    color: var(--ink-light);
    line-height: 1;
  }
  .wordmark-text .line-1 { display: block; font-size: 38px; letter-spacing: 2px; }
  .wordmark-text .line-2 { display: block; font-size: 21px; letter-spacing: 2.4px; margin-top: 4px; }

  .contact {
    position: absolute;
    left: 350px;
    top: 150px;
    color: var(--ink-light);
  }
  .contact-name {
    font-family: "Exo 2", sans-serif;
    font-weight: 600;
    font-size: 21px;
    color: var(--accent-blue);
  }
  .contact-title { font-size: 15px; color: var(--ink-muted); margin-bottom: 12px; }
  .contact-list { list-style: none; }
  .contact-list li {
    display: flex;
    align-items: center;
    gap: 10px;
    font-size: 15px;
    line-height: 24px;
  }
  .contact-list svg { width: 13px; height: 13px; fill: var(--ink-muted); flex: none; }

  .address-band {
    position: absolute;
    left: 0; right: 0; bottom: 0;
    height: 58px;
    background: linear-gradient(90deg, var(--band-start), var(--band-end));
    display: flex;
    align-items: center;
    padding-left: 40px;
    font-size: 16px;
    color: var(--ink-light);
  }
</style>
</head>
<body>
  <section class="card card-front">
    <div class="front-name"><span class="dot"></span>NORTHVALE</div>
  </section>

  <section class="card card-back">
    <div class="wordmark">
      <span class="dot"></span>
      <span class="wordmark-text">
        <span class="line-1">NORTHVALE</span>
        <span class="line-2">SPINE CARE</span>
      </span>
    </div>

    <div class="contact">
      <div class="contact-name">Mara Ellison</div>
      <div class="contact-title">Managing Director</div>
      <ul class="contact-list">
        <li>
          <svg viewBox="0 0 16 16" aria-hidden="true"><path d="M3.6 1.2l2.4 2.6-1.3 2a9 9 0 005.5 5.5l2-1.3 2.6 2.4-1.6 2.2C7.4 14.8 1.2 8.6.8 2.8z"/></svg>
          555-014-2290
        </li>
        <li>
          <svg viewBox="0 0 16 16" aria-hidden="true"><path d="M1 3h14v10H1z M1.5 3.5L8 9l6.5-5.5" fill="none" stroke="#d6d6d8" stroke-width="1.6"/></svg>
          mara@northvalespine.com
        </li>
        <li>
          <svg viewBox="0 0 16 16" aria-hidden="true"><circle cx="8" cy="8" r="6.5" fill="none" stroke="#d6d6d8" stroke-width="1.4"/><path d="M1.5 8h13M8 1.5c-3 3.5-3 9.5 0 13M8 1.5c3 3.5 3 9.5 0 13" fill="none" stroke="#d6d6d8" stroke-width="1.2"/></svg>
          www.northvalespine.com
        </li>
      </ul>
    </div>

    <div class="address-band">18 Harbor Lane, Westfield, Lakeview, US 402187</div>
  </section>
</body>
</html>
```